Bramblewood Card Company Business Cards

We are a trading card store with Glimmorax, sports and other TCG cards, we need a business card design that encompasses a clean cut, modern style with a retro flare. website is bramblewoodcardco.com for reference. Can utilize a comic book era feel or a more modern outdoor feel to utilize the "Pacific Northwest" elements of tress, mountains, etc.

Industry/Entity Type

Trading cards and collectibles

Contact Information for Business Card

business name, email address, phone number, name, owner job title

Font styles to use
Sans Serif

```html
<!DOCTYPE html>
<html lang="en">
<head>
<meta charset="utf-8">
<title>Bramblewood Card Company – Business Cards</title>
<link rel="stylesheet" href="https://fonts.googleapis.com/css2?family=Mulish:wght@400;600;800&display=swap">
<style>
  :root {
    --backdrop: #d6d6d6;
    --card: #ffffff;
    --cyan: #1fbde0;
    --slate: #6b6b6d;
    --ink: #2a2a2c;
  }
  * { box-sizing: border-box; margin: 0; padding: 0; }
  html, body {
    width: 1200px; height: 1018px; overflow: hidden;
    background: var(--backdrop);
    font-family: "Mulish", sans-serif;
  }
  .sheet {
    width: 1200px; height: 1018px;
    display: flex; flex-direction: column; align-items: center; justify-content: center;
    gap: 30px;
  }
  .card {
    position: relative;
    width: 820px; height: 468px;
    background: var(--card);
    box-shadow: 0 10px 30px rgba(0,0,0,0.12);
    overflow: hidden;
  }

  /* wordmark standing in for the brand mark */
  .wordmark {
    display: flex; align-items: center; gap: 14px;
    color: var(--slate);
    font-weight: 800;
    text-transform: uppercase;
    line-height: 1.05;
  }
  .wordmark__dot {
    flex: none;
    width: 26px; height: 26px; border-radius: 50%;
    background: var(--slate);
  }

  /* front */
  .card--front .wordmark {
    position: absolute; left: 56px; top: 70px;
    font-size: 30px; width: 320px;
  }
  .band { position: absolute; }
  .band--cyan {
    left: 0; top: 318px; width: 386px; height: 28px;
    background: var(--cyan);
    clip-path: polygon(0 0, 100% 0, 94% 100%, 0 100%);
  }
  .band--slate {
    left: 368px; top: 360px; width: 360px; height: 28px;
    background: var(--slate);
    clip-path: polygon(0 0, 100% 0, 100% 100%, 6% 100%);
  }
  .contact {
    position: absolute; right: 52px; top: 92px;
    text-align: right; color: var(--ink);
  }
  .contact__name {
    color: var(--cyan); font-weight: 600;
    font-size: 34px; letter-spacing: 1px; text-transform: uppercase;
  }
  .contact__role { font-size: 17px; margin-top: 2px; }
  .contact__address { font-size: 17px; line-height: 1.35; margin-top: 16px; }
  .contact__lines { list-style: none; margin-top: 26px; font-size: 17px; line-height: 1.4; }
  .contact__lines li { display: flex; justify-content: flex-end; align-items: center; gap: 8px; }
  .contact__lines svg { width: 14px; height: 14px; fill: var(--cyan); flex: none; }

  /* back */
  .card--back { display: flex; align-items: center; justify-content: center; }
  .card--back .wordmark { font-size: 40px; width: 440px; }
  .card--back .wordmark__dot { width: 34px; height: 34px; }
</style>
</head>
<body>
<main class="sheet">

  <section class="card card--front" aria-label="Business card front">
    <div class="wordmark"><span class="wordmark__dot"></span><span>Bramblewood Card Company</span></div>

    <div class="band band--cyan"></div>
    <div class="band band--slate"></div>

    <div class="contact">
      <h1 class="contact__name">Jonah Reyes</h1>
      <p class="contact__role">Founder</p>
      <p class="contact__address">482 Cedar Ridge Lane<br>Your Country, MN 46150</p>
      <ul class="contact__lines">
        <li>+012 555 0147
          <svg viewBox="0 0 16 16" aria-hidden="true"><path d="M4 1h8a1 1 0 0 1 1 1v12a1 1 0 0 1-1 1H4a1 1 0 0 1-1-1V2a1 1 0 0 1 1-1zm1 2v9h6V3zm3 10.2a.8.8 0 1 0 0-.01z"/></svg>
        </li>
        <li>+012 5550 1829
          <svg viewBox="0 0 16 16" aria-hidden="true"><path d="M2 6c0-2 3-3 6-3s6 1 6 3v1h-3V6H5v1H2zm2 2h8l2 6H2zm4 1.5a2 2 0 1 0 0 4 2 2 0 0 0 0-4z"/></svg>
        </li>
        <li>hello@bramblewoodcardco.com
          <svg viewBox="0 0 16 16" aria-hidden="true"><path d="M1 3h14v10H1zm1.5 1.3V5l5.5 4 5.5-4v-.7z"/></svg>
        </li>
        <li>www.bramblewoodcardco.com
          <svg viewBox="0 0 16 16" aria-hidden="true"><path d="M8 1a7 7 0 1 0 0 14A7 7 0 0 0 8 1zm0 1.5c.8 0 1.7 1.7 2 4.5H6c.3-2.8 1.2-4.5 2-4.5zM2.6 7h2c.1-1.5.4-2.9.9-3.9A5.5 5.5 0 0 0 2.6 7zm8.8 0h2a5.5 5.5 0 0 0-2.9-3.9c.5 1 .8 2.4.9 3.9zM2.6 9a5.5 5.5 0 0 0 2.9 3.9c-.5-1-.8-2.4-.9-3.9zm3.4 0c.3 2.8 1.2 4.5 2 4.5s1.7-1.7 2-4.5zm5.4 0c-.1 1.5-.4 2.9-.9 3.9A5.5 5.5 0 0 0 13.4 9z"/></svg>
        </li>
      </ul>
    </div>
  </section>

  <section class="card card--back" aria-label="Business card back">
    <div class="wordmark"><span class="wordmark__dot"></span><span>Bramblewood Card Company</span></div>
  </section>

</main>
</body>
</html>
```